Heron Property Inspection business card

I am the principal inspector of Heron Property Inspections. I serve Northern Virginia from Winchester to Arlington.Associate, Federated Guild of Dwelling Examiners (FGDE)Graduate, FGDE Home Inspectors CourseNational Association of Home Inspectors ExamI'd like the business card to look more professional than comical.I pulled the attached picture off the web. I'd like to have something like that or an image of a house as my logo on the cards.

Target Market(s)

Persons who recently purchased a home.

Industry/Entity Type

Business

Contact Information for Business Card

Bob AllenBadger Home Inspections, LLC.4455 River RoadBluemont, Virginia 20135cell: 703-231-6680e-mail: tkmarlow@postvale.net

Font styles to use
Serif
Sans Serif

Requirements
Must have
• I'd like to have a logo, something that identifies me as a home inspector. The attached images are something that I'd like to have incorporated into my business card logo.
Nice to have
• I'd like a sketch of a house and/or a magnifying glass showing a house being inspected. The attached images are used as a suggestion only, I do not own the images.
Should not have
• Gimmicky stuff. I want to appear professional and trustworthy.

```html
<!DOCTYPE html>
<html lang="en">
<head>
<meta charset="utf-8">
<title>Heron Property Inspections – Business Card</title>
<link rel="stylesheet" href="https://fonts.googleapis.com/css2?family=Open+Sans:wght@400;600&display=swap">
<style>
  :root {
    --page-bg: #e9e6e1;
    --card-white: #f4f4f3;
    --brand-red: #c41a1a;
    --band-red: #b81717;
    --ink-dark: #4a4a4a;
    --ink-mid: #5b5b5b;
  }
  * { box-sizing: border-box; margin: 0; padding: 0; }
  html, body {
    width: 1200px; height: 892px; overflow: hidden;
    background: var(--page-bg);
  }
  .canvas {
    width: 1200px; height: 892px;
    display: flex; align-items: center; justify-content: center;
  }
  .card {
    position: relative;
    width: 1000px; height: 572px;
    background: var(--card-white);
    border-radius: 34px;
    overflow: hidden;
    box-shadow: 0 10px 30px rgba(0,0,0,0.18);
    font-family: "Open Sans", Arial, sans-serif;
  }
  .card__band {
    position: absolute; top: 0; bottom: 0; width: 96px;
    background: var(--band-red);
  }
  .card__band--left { left: 0; }
  .card__band--right { right: 0; }
  .card__content {
    position: absolute; left: 250px; top: 92px;
  }
  .brand {
    display: flex; align-items: center; gap: 16px;
    padding-bottom: 10px;
    border-bottom: 4px solid var(--brand-red);
    width: 470px;
  }
  .brand__mark {
    width: 34px; height: 34px; background: var(--brand-red); flex: none;
  }
  .brand__name {
    font-size: 33px; font-weight: 600; line-height: 1.15;
    color: var(--ink-dark);
  }
  .person { margin-top: 34px; }
  .person__name {
    font-size: 50px; font-weight: 400; line-height: 1.05;
    color: var(--brand-red);
  }
  .person__title {
    margin-top: 6px; margin-left: 112px;
    font-size: 20px; color: var(--ink-mid);
  }
  .contact {
    margin-top: 42px; list-style: none;
    font-size: 26px; line-height: 1.5; color: var(--ink-mid);
  }
</style>
</head>
<body>
  <main class="canvas">
    <section class="card" aria-label="Heron Property Inspections business card">
      <div class="card__band card__band--left"></div>
      <div class="card__band card__band--right"></div>
      <div class="card__content">
        <header class="brand">
          <span class="brand__mark" aria-hidden="true"></span>
          <span class="brand__name">Heron Property Inspections, LLC</span>
        </header>
        <div class="person">
          <p class="person__name">Employee name</p>
          <p class="person__title">Managing Director</p>
        </div>
        <ul class="contact">
          <li>703-555-0192</li>
          <li>tkmarlow@postvale.net</li>
          <li>7182 Quarry Lane Fernhill, Virginia 20148</li>
        </ul>
      </div>
    </section>
  </main>
</body>
</html>
```